** Wanted ** Wordpress web design for scaffolding rental and construction company

We need a website design and must be functional to show a basic overview of what our company offers as a service. We have a domain name and a logo but we need web design. This web site should have another scaffolding rental page for construction and renovation as well as a quote section where customers can enter their personal information and also upload photos. The site% 26quot; www.brindlework.com% 26quot; should be intuitive, clear and classy ... The logo must be found on the site in several ways.

Target Market(s)

Professional and no professional

Coding

Coded - Design and coding required

Number of Pages Required

3 page

Font styles to use
Serif
Sans Serif
Decorative
Script

Requirements
Must have
• Our logo
Nice to have
• Slogan:% 26quot; The height% 26 # 224; port% 26 # 233; e hand% 26quot;

```html
<!DOCTYPE html>
<html lang="en">
<head>
<meta charset="utf-8">
<title>Brindlework – Scaffolding Rental</title>
<link rel="stylesheet" href="https://fonts.googleapis.com/css2?family=Poppins:wght@400;500;600;700;800&family=Open+Sans:wght@400;600&display=swap">
<style>
:root{
  --blue:#1787d9;
  --blue-deep:#1479c7;
  --nav-blue:#1e88e5;
  --orange:#ee6c1a;
  --ink:#141414;
  --body:#3a3a3a;
  --grey-bg:#f4f2f2;
  --white:#ffffff;
  --dark:#1c2433;
}
*{margin:0;padding:0;box-sizing:border-box}
html,body{width:1200px;height:3732px;overflow:hidden}
body{position:relative;background:var(--white);font-family:"Open Sans",Arial,sans-serif;color:var(--body)}
.abs{position:absolute}
.heading{font-family:"Poppins",Arial,sans-serif;font-weight:700;color:var(--ink);letter-spacing:-.3px}
.btn{position:absolute;background:var(--orange);color:var(--white);font-family:"Poppins",Arial,sans-serif;font-weight:600;display:flex;align-items:center;justify-content:center;text-transform:uppercase}
.rule{position:absolute;height:3px;width:65px;background:var(--nav-blue)}

/* header */
.site-header{position:absolute;left:0;top:0;width:1200px;height:109px;background:var(--white);z-index:5}
.brand-box{position:absolute;left:120px;top:0;width:231px;height:138px;background:var(--white);z-index:6;display:flex;align-items:center;justify-content:center;gap:10px;box-shadow:0 2px 6px rgba(0,0,0,.08)}
.brand-mark{width:18px;height:18px;background:var(--nav-blue)}
.brand-name{font-family:"Poppins",Arial,sans-serif;font-weight:700;font-size:24px;color:var(--nav-blue);letter-spacing:.5px}
.call{position:absolute;left:714px;top:20px;display:flex;gap:10px;align-items:center}
.call small{display:block;font-size:11px;color:var(--ink)}
.call strong{display:block;font-family:"Poppins",Arial,sans-serif;font-weight:500;font-size:19px;color:var(--ink);line-height:1.1}
.quote-btn{left:908px;top:20px;width:161px;height:35px;background:var(--nav-blue);font-size:14px}
.nav{position:absolute;top:76px;left:0;font-family:"Poppins",Arial,sans-serif;font-weight:600;font-size:14.5px;color:var(--ink)}
.nav span{position:absolute;white-space:nowrap}
.nav .active{color:var(--nav-blue);text-decoration:underline;text-underline-offset:4px}

/* hero */
.hero{position:absolute;left:0;top:109px;width:1200px;height:571px;clip-path:polygon(0 0,100% 0,100% 485px,600px 571px,0 485px);background:linear-gradient(160deg,#2c6fc2 0%,#3b86d6 40%,#4f93d8 70%,#5a9ad2 100%)}
.hero-photo{position:absolute;left:0;top:0;width:720px;height:571px;background:radial-gradient(ellipse at 45% 55%,rgba(196,150,60,.55),rgba(60,110,190,0) 70%)}
.hero-title{position:absolute;left:694px;top:212px;font-family:"Poppins",Arial,sans-serif;font-weight:800;font-size:55px;line-height:60px;color:var(--white);text-shadow:2px 3px 6px rgba(0,0,0,.45);z-index:2}
.file-field{position:absolute;left:698px;top:352px;width:370px;height:57px;background:var(--white);box-shadow:0 3px 8px rgba(0,0,0,.25);display:flex;align-items:center;padding-left:20px;font-family:"Poppins",Arial,sans-serif;font-weight:600;font-size:15px;color:#333;z-index:2}
.file-field .sep{position:absolute;left:310px;top:12px;width:1px;height:33px;background:#bbb}
.file-field svg{position:absolute;left:327px;top:17px}
.upload-btn{left:701px;top:435px;width:128px;height:48px;font-size:20px;border:2px solid var(--white);z-index:2}
.dots{position:absolute;left:548px;top:610px;display:flex;gap:12px;align-items:center;z-index:3}
.dots i{display:block;width:8px;height:8px;border-radius:50%;background:var(--white)}
.dots i.on{width:13px;height:13px;background:transparent;border:2px solid var(--white)}

/* services */
.section-title{position:absolute;left:0;width:1200px;text-align:center;font-size:27px}
.card{position:absolute;width:455px;height:188px;border:2px solid var(--nav-blue);background:var(--white)}
.card .icon{position:absolute;left:34px;top:36px}
.card .divider{position:absolute;left:148px;top:30px;width:1px;height:126px;background:#bbb}
.card h3{position:absolute;left:185px;top:32px;font-family:"Poppins",Arial,sans-serif;font-weight:600;font-size:15px;color:var(--ink)}
.card p{position:absolute;left:185px;top:62px;width:245px;font-size:12.5px;line-height:17.5px;color:#333}
.card .btn{left:185px;top:131px;height:24px;padding:0 9px;font-size:11px}

/* welcome */
.welcome{position:absolute;left:0;top:1298px;width:1200px;height:520px;background:var(--grey-bg)}
.welcome-photo{position:absolute;left:0;top:0;width:640px;height:520px;background:linear-gradient(90deg,#8b8b88 0%,#a5a39f 45%,#cfccc9 80%,var(--grey-bg) 100%)}
.welcome small{position:absolute;left:648px;top:66px;font-family:"Poppins",Arial,sans-serif;font-weight:500;font-size:19px;color:var(--ink)}
.welcome h2{position:absolute;left:648px;top:92px;font-size:38px}
.welcome p{position:absolute;left:648px;top:189px;width:420px;font-size:14.5px;line-height:21px;color:#333}
.welcome .btn{left:648px;top:392px;width:119px;height:37px;font-size:15px}

/* why choose */
.why{position:absolute;left:0;top:1720px;width:1200px;height:745px;background:var(--blue);clip-path:polygon(0 11px,608px 91px,100% 8px,100% 656px,600px 743px,0 656px)}
.why .section-title{color:var(--white)}
.why .rule{background:var(--white)}
.feature{position:absolute;width:245px;color:var(--white)}
.feature h3{position:absolute;left:0;top:0;height:44px;display:flex;align-items:center;gap:18px;font-family:"Poppins",Arial,sans-serif;font-weight:600;font-size:19px;white-space:nowrap}
.feature p{position:absolute;left:0;top:60px;width:245px;font-size:13.5px;line-height:19.5px}
.feature .line{position:absolute;left:0;top:146px;width:240px;height:3px;background:var(--white)}

/* projects */
.project{position:absolute;top:2676px;width:225px;height:225px}

/* call-to-action */
.cta{position:absolute;left:0;top:2920px;width:1200px;height:470px;background:linear-gradient(180deg,#1b2230 0%,#2a3446 55%,#33415a 100%);clip-path:polygon(0 0,100% 0,100% 384px,600px 468px,0 384px)}
.cta h2{position:absolute;left:133px;top:72px;font-size:27px;line-height:38px;color:var(--white)}
.cta .rule{left:133px;top:159px}
.cta p{position:absolute;left:133px;top:201px;width:380px;font-size:18.5px;line-height:26px;color:var(--white)}
.cta .contact-btn{left:133px;top:275px;width:152px;height:45px;font-size:18px}
.field{position:absolute;left:661px;width:407px;background:var(--white);font-family:"Poppins",Arial,sans-serif;font-size:12.5px;color:#333;padding:14px 16px}
.cta .get-btn{left:662px;top:307px;width:158px;height:43px;font-size:18px}

/* footer */
.footer{position:absolute;left:0;top:3300px;width:1200px;height:432px;background:var(--blue);clip-path:polygon(0 4px,600px 88px,100% 4px,100% 100%,0 100%)}
.footer-brand{position:absolute;left:133px;top:3498px;width:248px;height:70px;border:3px solid var(--white);display:flex;align-items:center;justify-content:center;gap:10px}
.footer-brand .brand-mark{background:var(--white)}
.footer-brand .brand-name{color:var(--white)}
.fdiv{position:absolute;top:3441px;width:2px;height:200px;background:var(--white)}
.fhead{position:absolute;top:3443px;font-family:"Poppins",Arial,sans-serif;font-weight:600;font-size:15px;color:var(--white)}
.social{position:absolute;top:3480px;width:25px;height:25px;border-radius:50%}
.menu{position:absolute;left:736px;top:3476px;list-style:none;font-size:12.5px;line-height:21px;color:var(--white)}
.contact-item{position:absolute;left:880px;display:flex;gap:12px;align-items:flex-start;font-size:13.5px;line-height:19px;color:var(--white)}
.contact-item .dot{width:28px;height:28px;border-radius:50%;background:var(--white);display:flex;align-items:center;justify-content:center;flex:none;margin-top:2px}
.copyright{position:absolute;left:0;top:3704px;width:1200px;text-align:center;font-size:11.5px;color:var(--white)}
</style>
</head>
<body>

<header class="site-header">
  <div class="call">
    <svg width="26" height="26" viewBox="0 0 24 24" aria-hidden="true"><path d="M6.6 10.8a15.1 15.1 0 0 0 6.6 6.6l2.2-2.2a1 1 0 0 1 1-.25 11.4 11.4 0 0 0 3.6.57 1 1 0 0 1 1 1V20a1 1 0 0 1-1 1A17 17 0 0 1 3 4a1 1 0 0 1 1-1h3.5a1 1 0 0 1 1 1c0 1.25.2 2.45.57 3.57a1 1 0 0 1-.25 1z" fill="none" stroke="#222" stroke-width="1.6"/></svg>
    <div><small>CALL US</small><strong>555.014.2288</strong></div>
  </div>
  <div class="btn quote-btn">Request a Quote</div>
  <nav class="nav">
    <span class="active" style="left:439px">HOME</span>
    <span style="left:511px">ABOUT US</span>
    <span style="left:620px">SERVICES</span>
    <span style="left:723px">SOLUTIONS</span>
    <span style="left:833px">TESTIMONIALS</span>
    <span style="left:978px">CONTACT US</span>
  </nav>
</header>
<div class="brand-box"><span class="brand-mark"></span><span class="brand-name">BRINDLEWORK</span></div>

<section class="hero">
  <div class="hero-photo" role="img" aria-label="Photo of a tall building wrapped in yellow scaffolding against a blue sky"></div>
</section>
<h1 class="hero-title">SCAFFOLDING<br>RENTAL</h1>
<div class="file-field">CHOOSE FILE<span class="sep"></span>
  <svg width="22" height="22" viewBox="0 0 24 24" aria-hidden="true"><path d="M12 3l6 6h-4v6h-4V9H6z M4 18h16v3H4z" fill="#333"/></svg>
</div>
<div class="btn upload-btn">Upload</div>
<div class="dots"><i></i><i></i><i class="on"></i><i></i><i></i></div>

<h2 class="heading section-title" style="top:732px">BRINDLEWORK SERVICES</h2>
<div class="rule" style="left:567px;top:784px"></div>

<article class="card" style="left:133px;top:839px">
  <svg class="icon" width="76" height="80" viewBox="0 0 76 80" fill="none" stroke="#1e88e5" stroke-width="2.5" aria-hidden="true"><path d="M8 2v76M68 2v76M8 14h60M8 40h60M8 66h60M8 14l60 26M68 14L8 40M8 40l60 26M68 40L8 66M38 2v76"/></svg>
  <span class="divider"></span>
  <h3>SCAFFOLDING</h3>
  <p>There are many variations of passa ges of Lorem Ipsum available, but the majority have suffered alteration.</p>
  <div class="btn">Read More</div>
</article>
<article class="card" style="left:613px;top:839px">
  <svg class="icon" width="76" height="80" viewBox="0 0 76 80" fill="none" stroke="#1e88e5" stroke-width="2.5" aria-hidden="true"><path d="M4 78V34h16V18h36v16h16v44zM20 34v44M56 34v44M30 78V60h16v18M24 2h28v16H24z"/><circle cx="38" cy="10" r="5"/><path d="M9 44h6M9 54h6M9 64h6M61 44h6M61 54h6M61 64h6M28 30h20M28 42h20"/></svg>
  <span class="divider"></span>
  <h3>CONSTRUCTION</h3>
  <p>There are many variations of passa ges of Lorem Ipsum available, but the majority have suffered alteration.</p>
  <div class="btn">Read More</div>
</article>
<article class="card" style="left:133px;top:1048px">
  <svg class="icon" width="76" height="80" viewBox="0 0 76 80" fill="none" stroke="#1e88e5" stroke-width="2.5" aria-hidden="true"><path d="M18 2v64M58 2v64M18 8h40M18 30h40M18 52h40M8 52h60v14H8z"/><circle cx="14" cy="72" r="5"/><circle cx="62" cy="72" r="5"/></svg>
  <span class="divider"></span>
  <h3>TEMPORARY ROOFS</h3>
  <p>There are many variations of passa ges of Lorem Ipsum available, but the majority have suffered alteration.</p>
  <div class="btn">Read More</div>
</article>
<article class="card" style="left:613px;top:1048px">
  <svg class="icon" width="76" height="80" viewBox="0 0 76 80" aria-hidden="true"><path d="M10 28c-6 6 0 22 14 36s30 20 36 14l4-6-12-10-6 6c-6-2-18-14-20-20l6-6-10-12z" fill="#1e88e5"/><circle cx="52" cy="20" r="17" fill="none" stroke="#1e88e5" stroke-width="3"/><circle cx="45" cy="20" r="2.5" fill="#1e88e5"/><circle cx="52" cy="20" r="2.5" fill="#1e88e5"/><circle cx="59" cy="20" r="2.5" fill="#1e88e5"/></svg>
  <span class="divider"></span>
  <h3>RENT A SCAFFOLDING</h3>
  <p>If you are interested, call to us at 0738 000 0123 or send message by email on info@brindlework.com.</p>
  <div class="btn">Contact Us</div>
</article>

<section class="welcome">
  <div class="welcome-photo" role="img" aria-label="Photo of a concrete building under construction beside a tall crane"></div>
  <small>WELCOME TO</small>
  <h2 class="heading">BRINDLEWORK</h2>
  <div class="rule" style="left:648px;top:147px;width:45px"></div>
  <p>Lorem ipsum dolor sit amet, consectetur adipiscing elit, sed do eiusmod tempor incididunt ut labore et dolore magna aliqua. Ut enim ad minim veniam, quis nostrud exercitation ullamco laboris nisi ut aliquip ex ea commodo consequat. Duis aute irure dolor in reprehenderit in voluptate velit esse cillum dolore eu fugiat nulla pariatur. Excepteur sint occaecat cupidatat non proident, sunt in culpa qui officia deserunt mollit anim id est laborum</p>
  <div class="btn">Read More</div>
</section>

<section class="why">
  <h2 class="heading section-title" style="top:153px">WHY CHOOSE BRINDLEWORK</h2>
  <div class="rule" style="left:567px;top:203px"></div>

  <div class="feature" style="left:133px;top:262px">
    <h3><svg width="44" height="44" viewBox="0 0 44 44" fill="none" stroke="#fff" stroke-width="3" aria-hidden="true"><circle cx="22" cy="22" r="19"/><circle cx="22" cy="22" r="13"/><path d="M15 22l5 5 9-10"/></svg>QUALITY</h3>
    <p>Lorem ipsum dolor sit amet, consec tetur adipiscing elit, sed do eiusmod tempor incididunt ut labore et dolore magna aliqua. Ut enim ad .</p>
    <span class="line"></span>
  </div>
  <div class="feature" style="left:482px;top:262px">
    <h3><svg width="44" height="44" viewBox="0 0 44 44" fill="none" stroke="#fff" stroke-width="2.5" aria-hidden="true"><path d="M4 42V14h12V2h24v40zM16 14v28M22 10h4M30 10h4M22 20h4M30 20h4M22 30h4M30 30h4M8 22h4M8 32h4"/></svg>EXPERIENCE</h3>
    <p>Lorem ipsum dolor sit amet, consec tetur adipiscing elit, sed do eiusmod tempor incididunt ut labore et dolore magna aliqua. Ut enim ad .</p>
    <span class="line"></span>
  </div>
  <div class="feature" style="left:830px;top:262px">
    <h3><svg width="54" height="44" viewBox="0 0 54 44" aria-hidden="true"><path d="M2 22C10 10 18 5 27 5s17 5 25 17c-8 12-16 17-25 17S10 34 2 22z" fill="#fff"/><circle cx="27" cy="22" r="10" fill="#1787d9"/><circle cx="27" cy="22" r="5" fill="#fff"/></svg>OUR VISION</h3>
    <p>Lorem ipsum dolor sit amet, consec tetur adipiscing elit, sed do eiusmod tempor incididunt ut labore et dolore magna aliqua. Ut enim ad .</p>
    <span class="line"></span>
  </div>

  <div class="feature" style="left:133px;top:485px">
    <h3><svg width="46" height="40" viewBox="0 0 46 40" fill="#fff" aria-hidden="true"><circle cx="14" cy="11" r="8"/><circle cx="32" cy="11" r="8"/><path d="M0 38c0-10 6-16 14-16s14 6 14 16zM18 38c0-10 6-16 14-16s14 6 14 16z"/></svg>MAN POWER</h3>
    <p>Lorem ipsum dolor sit amet, consec tetur adipiscing elit, sed do eiusmod tempor incididunt ut labore et dolore magna aliqua. Ut enim ad .</p>
  </div>
  <div class="feature" style="left:482px;top:485px">
    <h3><svg width="50" height="36" viewBox="0 0 50 36" fill="#fff" aria-hidden="true"><path d="M8 26c0-12 7-20 17-20s17 8 17 20z"/><rect x="2" y="28" width="46" height="6"/></svg>WORKER SAFETY</h3>
    <p>Lorem ipsum dolor sit amet, consec tetur adipiscing elit, sed do eiusmod tempor incididunt ut labore et dolore magna aliqua. Ut enim ad .</p>
  </div>
  <div class="feature" style="left:830px;top:485px">
    <h3><svg width="44" height="44" viewBox="0 0 44 44" fill="none" stroke="#fff" stroke-width="3" aria-hidden="true"><circle cx="22" cy="22" r="19"/><path d="M22 10v13l7 6"/></svg>TIMELY HANDOVER</h3>
    <p>Lorem ipsum dolor sit amet, consec tetur adipiscing elit, sed do eiusmod tempor incididunt ut labore et dolore magna aliqua. Ut enim ad .</p>
  </div>
</section>

<h2 class="heading section-title" style="top:2520px;line-height:39px">BRINDLEWORK PROJECTS WE HAVE<br>DELIVERED ACROSS WORLD</h2>
<div class="rule" style="left:578px;top:2619px;width:44px"></div>

<div class="project" style="left:10px;background:linear-gradient(180deg,#3f7fc4,#9ab6d2 55%,#9c9a92)" role="img" aria-label="Photo of a tower crane over a building site"></div>
<div class="project" style="left:248px;background:linear-gradient(160deg,#e69a3a,#9b6a45 40%,#6b5a52 100%)" role="img" aria-label="Photo of scaffolding on a building facade at sunset"></div>
<div class="project" style="left:486px;background:linear-gradient(180deg,#4d86c8,#8aa0b4 50%,#6f7378)" role="img" aria-label="Photo of a building covered in scaffolding"></div>
<div class="project" style="left:724px;background:linear-gradient(180deg,#2f74c8,#7ea8d6 55%,#8a7a6d)" role="img" aria-label="Photo of a high-rise under construction with a red crane"></div>
<div class="project" style="left:962px;background:linear-gradient(180deg,#6a9fd8,#b3c9de 50%,#5d6672)" role="img" aria-label="Photo of a steel frame structure against the sky"></div>

<section class="cta" role="img" aria-label="Dark photo of a scaffolded building behind the contact form">
  <h2 class="heading">NEED IMMEDIATE ASSISTANCE ?<br>CALL US NOW!</h2>
  <div class="rule"></div>
  <p>Lorem ipsum dolor sit amet, consec tetur adipiscing elit, sed do eiusmod tempo.</p>
  <div class="btn contact-btn">Contact Us</div>
  <div class="field" style="top:77px;height:43px">FULL NAME</div>
  <div class="field" style="top:132px;height:42px">E MAIL ADDRESS</div>
  <div class="field" style="top:185px;height:100px">MESSAGE</div>
  <div class="btn get-btn">Get a Quote</div>
</section>

<footer class="footer"></footer>
<div class="footer-brand"><span class="brand-mark"></span><span class="brand-name">BRINDLEWORK</span></div>
<span class="fdiv" style="left:501px"></span>
<span class="fdiv" style="left:691px"></span>
<span class="fdiv" style="left:838px"></span>
<div class="fhead" style="left:542px">FOLLOW US</div>
<span class="social" style="left:542px;background:#2a4f9a"></span>
<span class="social" style="left:576px;background:#2f9ae6"></span>
<span class="social" style="left:611px;background:#16325f"></span>
<div class="fhead" style="left:736px">MENU</div>
<ul class="menu"><li>Home</li><li>About Us</li><li>Services</li><li>Soutions</li><li>Blog</li><li>Contact us</li></ul>
<div class="fhead" style="left:880px">CONTACT US</div>
<div class="contact-item" style="top:3481px"><span class="dot"><svg width="12" height="16" viewBox="0 0 12 16" aria-hidden="true"><path d="M6 0a6 6 0 0 1 6 6c0 4-6 10-6 10S0 10 0 6a6 6 0 0 1 6-6z" fill="#1787d9"/><circle cx="6" cy="6" r="2" fill="#fff"/></svg></span><span>2150 Harbor Lane<br>Fairview, CA 90000</span></div>
<div class="contact-item" style="top:3544px"><span class="dot"><svg width="14" height="14" viewBox="0 0 24 24" aria-hidden="true"><path d="M6.6 10.8a15.1 15.1 0 0 0 6.6 6.6l2.2-2.2a1 1 0 0 1 1-.25 11.4 11.4 0 0 0 3.6.57 1 1 0 0 1 1 1V20a1 1 0 0 1-1 1A17 17 0 0 1 3 4a1 1 0 0 1 1-1h3.5a1 1 0 0 1 1 1c0 1.25.2 2.45.57 3.57a1 1 0 0 1-.25 1z" fill="#1787d9"/></svg></span><span>Call Us<br>555.014.2288</span></div>
<div class="contact-item" style="top:3605px"><span class="dot"><svg width="14" height="11" viewBox="0 0 14 11" aria-hidden="true"><rect x="0" y="0" width="14" height="11" rx="1" fill="#1787d9"/><path d="M1 1l6 5 6-5" fill="none" stroke="#fff" stroke-width="1.4"/></svg></span><span>E mail Us<br>hello@brindlework.com</span></div>
<div class="copyright">Copyright © 2020 All Rights Reserved</div>

</body>
</html>
```